Varnik Holdings — Business Card Design Brief
Overview
Design a double-sided business card for Varnik Holdings that highlights our two service arms: Varnik Communications (telecommunications) and Varnik Energy (business energy solutions). The card should feel smart and stand out when handed to clients.

Objectives
Showcase our areas of specialty clearly.
Reflect the overall Varnik / Varnik Holdings brand while acknowledging both arms.
Explore using both logos (Communications + Energy) or one unified logo, depending on the design.

Deliverables
One double-sided business card design (front + back).

Content & Copy
Front (preferred): Logo: Varnik / Varnik Holdings
Descriptor: Business Communications | Business Energy
Back:My contact details and company details
Core products: Business Mobile • Telephony • Internet • Business Energy Solutions

Brand & Visual Direction
We have a group logo currently tailored more toward telecoms, plus a separate Varnik Energy logo.
Please explore layouts that use both logos or just one, whichever works best.
Color: I wouldn't mind seeing an option using our the Blue/Purple gradient from our website (varnik-example.co.uk), but also open to non-gradient approaches and other colours..

Overall look: Smart, modern, and distinctive.
Format & Print Specs
Double-sided business card format. (Use a standard size

Must-Haves
Front: Varnik wording or Varnik Holdings wording with atleast 1 logo also on front “Business Communications | Business Energy.”

Back: Contact + company details and core products.
A design that stands out while remaining professional.

Nice-to-Have Options
A gradient version using our site’s Blue/Purple gradient.
A non-gradient version.
A dual-logo treatment versus a single-logo treatment.

Thanks
Owen

```html
<!DOCTYPE html>
<html lang="en">
<head>
<meta charset="utf-8">
<title>Varnik Business Card</title>
<link rel="stylesheet" href="https://fonts.googleapis.com/css2?family=Montserrat:wght@400;500;700;800&display=swap">
<style>
  :root {
    --bg: #9a9a9a;
    --purple: #84449a;
    --blue: #0d68a8;
    --navy: #1b2f5e;
    --ink: #241e5e;
    --white: #ffffff;
    --cyan: #1aa3dc;
    --green: #4fb24a;
    --mark-blue: #2f74c0;
  }
  * { margin: 0; padding: 0; box-sizing: border-box; }
  html, body { width: 1200px; height: 1108px; overflow: hidden; }
  body {
    background: var(--bg);
    font-family: "Montserrat", Arial, sans-serif;
    color: var(--white);
    position: relative;
  }
  .card {
    position: absolute;
    left: 242px;
    width: 716px;
    height: 409px;
    border-radius: 28px;
    overflow: hidden;
    background: linear-gradient(118deg, var(--purple) 0%, var(--purple) 42%, #5a56a8 52%, var(--blue) 60%, var(--navy) 72%, var(--navy) 100%);
  }
  .card--front { top: 119px; }
  .card--back { top: 581px; }

  /* front */
  .brand-lockup {
    position: absolute;
    left: 0; right: 0; top: 96px;
    display: flex; flex-direction: column; align-items: center;
  }
  .brand-lockup__dot {
    width: 130px; height: 130px; border-radius: 50%;
    background: var(--green);
    margin-bottom: 18px;
  }
  .brand-lockup__name {
    font-weight: 800; font-size: 66px; letter-spacing: 1px;
    color: var(--ink); line-height: 1;
  }
  .descriptor {
    position: absolute; left: 0; right: 0; top: 352px;
    text-align: center; font-size: 19px; font-weight: 400; letter-spacing: 0.4px;
  }

  /* back */
  .division {
    position: absolute; left: 52px; top: 66px; width: 258px;
    display: flex; flex-direction: column; align-items: center;
  }
  .division__dot {
    width: 110px; height: 110px; border-radius: 50%;
    background: var(--mark-blue); margin-bottom: 34px;
  }
  .division__name {
    font-weight: 800; color: var(--white); text-align: center; line-height: 1;
  }
  .division__name-main { display: block; font-size: 56px; letter-spacing: 1px; }
  .division__name-sub { display: block; font-size: 19.5px; letter-spacing: 3.2px; margin-top: 8px; }
  .divider {
    position: absolute; left: 337px; top: 57px; width: 2px; height: 249px;
    background: var(--cyan);
  }
  .contact { position: absolute; left: 366px; top: 54px; }
  .contact__name { font-weight: 700; font-size: 33px; line-height: 1.1; }
  .contact__role { font-size: 18px; margin-top: 6px; }
  .contact__address { font-size: 18px; line-height: 29px; margin-top: 16px; }
  .contact__list { list-style: none; margin-top: 12px; }
  .contact__list li {
    font-size: 18px; line-height: 28.5px;
    display: flex; align-items: center; gap: 8px;
  }
  .contact__list svg { width: 15px; height: 15px; flex: none; fill: var(--cyan); }
  .products {
    position: absolute; left: 0; right: 0; top: 350px;
    text-align: center; font-size: 16.5px; font-weight: 400; letter-spacing: 0.3px;
  }
</style>
</head>
<body>
  <section class="card card--front" aria-label="Card front">
    <div class="brand-lockup">
      <span class="brand-lockup__dot"></span>
      <span class="brand-lockup__name">VARNIK</span>
    </div>
    <p class="descriptor">Business Communications | Business Energy</p>
  </section>

  <section class="card card--back" aria-label="Card back">
    <div class="division">
      <span class="division__dot"></span>
      <p class="division__name">
        <span class="division__name-main">VARNIK</span>
        <span class="division__name-sub">COMMUNICATIONS</span>
      </p>
    </div>
    <div class="divider"></div>
    <div class="contact">
      <h1 class="contact__name">Daniel Ashcroft</h1>
      <p class="contact__role">Managing Director</p>
      <p class="contact__address">24 Harrow Lane, Leeds,<br>England, LS2 7QT</p>
      <ul class="contact__list">
        <li>
          <svg viewBox="0 0 16 16" aria-hidden="true"><path d="M3.5 1.5l2.3 2.6-1.3 1.7c.9 2 2.4 3.6 4.5 4.6l1.6-1.3 2.7 2.2-1.4 2.3C6.8 13.4 2.6 9.2 1.4 3z"/></svg>
          +44 0113 496 0123
        </li>
        <li>
          <svg viewBox="0 0 16 16" aria-hidden="true"><path d="M8 1a7 7 0 0 0-6 10.6L1 15l3.5-1A7 7 0 1 0 8 1zm0 1.5a5.5 5.5 0 1 1-3 10.1l-1.7.5.5-1.6A5.5 5.5 0 0 1 8 2.5z"/></svg>
          +44 7700 900 456 (Live Chat)
        </li>
        <li>
          <svg viewBox="0 0 16 16" aria-hidden="true"><path d="M1 3.5h14v9H1z"/><path d="M1.5 4l6.5 5 6.5-5" fill="none" stroke="#1b2f5e" stroke-width="1"/></svg>
          info@varnik-example.co.uk
        </li>
        <li>
          <svg viewBox="0 0 16 16" aria-hidden="true"><circle cx="8" cy="8" r="6.5" fill="none" stroke="var(--cyan)" stroke-width="1.6"/><path d="M1.5 8h13M8 1.5c-2.5 3.5-2.5 9.5 0 13M8 1.5c2.5 3.5 2.5 9.5 0 13" fill="none" stroke="var(--cyan)" stroke-width="1.2"/></svg>
          varnik-example.co.uk
        </li>
      </ul>
    </div>
    <p class="products">Business Mobile • Telephony • Internet • Business Energy Solutions</p>
  </section>
</body>
</html>
```